Business Card Design

Hi I need a business card designed, we already have the business name logo artwork and would like some concept ideas for the Bus Card layout.
On the back of the card i want to include the products and services that we offer.
We are a Plastics Sheeting manufacture based in Perth Australia.

                                       

We need a BC design for a company called Tarvo Plastics based in Perth Australia.

We supply from DIY to Trade & Industrial  Engineering Markets.

We specialise in:

·         Cut to size panels  (all shapes and sizes)

·         Plastics fabrication & Welding

·         Custom Designs

·         Plastic Repairs

·         PVC Pipe Slotting & PVC Pipe Threading

·         Supplier of all types of engineering plastics and profiles.

Including:           Acrylic / Clarvene

                               Polycarbonate / Dorvil

                               Prismatic Light Diffuser

                               Vantrib

                               HDPE / UHMWPE

                               PVC / PVC Foam

                               Nylon

                               HIPS

```html
<!DOCTYPE html>
<html lang="en">
<head>
<meta charset="utf-8">
<title>Tarvo Plastics – Business Card</title>
<link rel="stylesheet" href="https://fonts.googleapis.com/css2?family=Open+Sans:wght@400;600;700;800&display=swap">
<style>
  :root {
    --navy: #0f2a5e;
    --mid-blue: #1e88c9;
    --band-blue: #2a8fd0;
    --pale-band: #5fb3e4;
    --white: #ffffff;
    --ink: #2c2c2c;
    --accent-orange: #e8762c;
    --bullet-red: #d3152a;
    --stage: #eef0f2;
  }
  * { margin: 0; padding: 0; box-sizing: border-box; }
  html, body {
    width: 1200px; height: 720px; overflow: hidden;
    background: var(--stage);
    font-family: "Open Sans", Arial, sans-serif;
  }
  .canvas {
    position: relative; width: 1200px; height: 720px;
    display: flex; align-items: center; justify-content: center; gap: 40px;
  }
  .card {
    position: relative; width: 540px; height: 309px; overflow: hidden;
    box-shadow: 0 6px 18px rgba(0,0,0,.18);
  }

  /* Front */
  .card-front { background: var(--white); }
  .card-front .swoosh { position: absolute; inset: 0; }
  .front-brand {
    position: absolute; left: 30px; top: 58px;
    display: flex; align-items: center; gap: 8px;
    color: var(--navy); font-weight: 800; font-size: 30px; letter-spacing: -0.4px;
    white-space: nowrap;
  }
  .brand-square { width: 18px; height: 18px; background: var(--navy); flex: none; }
  .holder {
    position: absolute; left: 40px; top: 150px; color: var(--ink);
  }
  .holder-name { font-size: 15px; font-weight: 700; color: var(--navy); }
  .holder-name .holder-title { font-size: 12px; font-weight: 600; color: var(--accent-orange); }
  .holder-address { margin-top: 6px; font-size: 12.5px; line-height: 1.35; }
  .holder-address + .holder-address { margin-top: 10px; }
  .contacts {
    position: absolute; right: 26px; top: 78px;
    list-style: none; color: var(--white); font-size: 12.5px; line-height: 1.55; text-align: right;
  }
  .contacts li { display: flex; justify-content: flex-end; align-items: center; gap: 6px; }
  .contacts svg { width: 11px; height: 11px; fill: var(--white); }
  .contacts .email { margin-top: 18px; }
  .trading-name {
    position: absolute; right: 22px; bottom: 14px;
    color: var(--white); font-size: 11.5px;
  }

  /* Back */
  .card-back { background: var(--mid-blue); color: var(--white); }
  .back-brand {
    position: absolute; left: 0; right: 0; top: 22px;
    display: flex; justify-content: center; align-items: center; gap: 10px;
    font-weight: 800; font-size: 38px; letter-spacing: -0.5px;
  }
  .back-brand .brand-square { background: var(--white); width: 20px; height: 20px; }
  .tagline {
    position: absolute; left: 0; right: 0; top: 84px;
    text-align: center; font-weight: 700; font-size: 12.5px; line-height: 1.3;
  }
  .offer-col { position: absolute; top: 130px; }
  .offer-col.services { left: 26px; width: 290px; }
  .offer-col.materials { left: 336px; width: 190px; }
  .divider { position: absolute; left: 322px; top: 126px; width: 1px; height: 124px; background: rgba(255,255,255,.7); }
  .col-heading { color: var(--navy); font-weight: 700; font-size: 14.5px; margin-bottom: 3px; }
  .offer-list { list-style: none; font-size: 12px; line-height: 1.38; }
  .offer-list li { position: relative; padding-left: 12px; }
  .offer-list li::before, .dot::before {
    content: ""; position: absolute; left: 0; top: 6px;
    width: 6px; height: 6px; border-radius: 50%; background: var(--bullet-red);
  }
  .dot { position: relative; padding-left: 12px; margin-left: 6px; }
</style>
</head>
<body>
<main class="canvas">

  <section class="card card-front" aria-label="Business card front">
    <svg class="swoosh" viewBox="0 0 540 309" preserveAspectRatio="none" aria-hidden="true">
      <path d="M300 0 C305 120 262 240 180 309 L204 309 C276 246 328 140 340 0 Z" fill="var(--pale-band)"/>
      <path d="M318 0 C320 126 276 244 194 309 L212 309 C284 248 334 140 352 0 Z" fill="var(--band-blue)"/>
      <path d="M350 0 C336 140 280 248 210 309 L540 309 L540 0 Z" fill="var(--navy)"/>
    </svg>
    <div class="front-brand"><span class="brand-square"></span>Tarvo Plastics</div>
    <div class="holder">
      <p class="holder-name">Your Name, <span class="holder-title">Title</span></p>
      <p class="holder-address">Unit 4/18 Merrow Way<br>Kelbrook WA 6152</p>
      <p class="holder-address">PO Box 2207 Kelbrook<br>DC WA 6961</p>
    </div>
    <ul class="contacts">
      <li><svg viewBox="0 0 12 12"><path d="M2 1h2.5l1 3-1.5 1a7 7 0 0 0 3 3l1-1.5 3 1V10a1 1 0 0 1-1 1A9 9 0 0 1 1 2a1 1 0 0 1 1-1z"/></svg>08 6104 3370</li>
      <li><svg viewBox="0 0 12 12"><rect x="3" y="0.5" width="6" height="11" rx="1"/></svg>0412 555 781</li>
      <li><svg viewBox="0 0 12 12"><rect x="1" y="5" width="10" height="6" rx="1"/><rect x="3" y="1" width="6" height="4"/></svg>08 6104 3372</li>
      <li>www.tarvoplastics.com.au</li>
      <li class="email"><svg viewBox="0 0 12 12"><rect x="0.5" y="2" width="11" height="8" rx="1"/></svg>sales@tarvoplastics.com.au</li>
    </ul>
    <p class="trading-name">Kelso Holdings Pty Ltd T/A Tarvo Plastics ABN:TBA</p>
  </section>

  <section class="card card-back" aria-label="Business card back">
    <div class="back-brand"><span class="brand-square"></span>Tarvo Plastics</div>
    <p class="tagline">The Products And Services That We Offer<br>Are Supplied From Diy To Trade &amp; Industrial Engineering Markets</p>

    <div class="offer-col services">
      <h2 class="col-heading">We specialise in:</h2>
      <ul class="offer-list">
        <li>Cut to size panels (all shapes and sizes)</li>
        <li>Plastics fabrication &amp; Welding</li>
        <li>Custom Designs</li>
        <li>Plastic Repairs</li>
        <li>PVC Pipe Slotting &amp; PVC Pipe Threading</li>
        <li>Supplier of all types of engineering plastics and profiles</li>
      </ul>
    </div>
    <div class="divider"></div>
    <div class="offer-col materials">
      <h2 class="col-heading">Including:</h2>
      <ul class="offer-list">
        <li>Acrylic / Clarvene</li>
        <li>Polycarbonate / Dorvil</li>
        <li>Prismatic Light Diffuser</li>
        <li>Vantrib <span class="dot">HDPE / UHMWPE</span></li>
        <li>PVC / PVC Foam</li>
        <li>Nylon <span class="dot">HIPS</span></li>
      </ul>
    </div>
  </section>

</main>
</body>
</html>
```